RUVO WARE LTD

Advertisement to get more schools:
use website https://www.ruvo-ware.co.uk for logos etc.
ICT Service Level Agreements for as little as £2000 per year
Unlimited Remote, phone and email support
Unlimited Call outs included
90% fix time within 30 minutes of ticket submission
Extra support during Scolvar inspections
GDPR service included

Education

```html
<!DOCTYPE html>
<html lang="en">
<head>
<meta charset="utf-8">
<title>RUVO WARE LTD – ICT Support for Education</title>
<link href="https://fonts.googleapis.com/css2?family=Poppins:wght@300;400;500;600;700&display=swap" rel="stylesheet">
<style>
  :root {
    --orange: #f2814a;
    --orange-pale: #fde3d6;
    --blue: #1c6db5;
    --ink: #2b2b2b;
    --text: #333333;
    --footer: #1d1c2c;
    --white: #ffffff;
    --card-shadow: 0 8px 18px rgba(0,0,0,0.13);
  }
  * { box-sizing: border-box; margin: 0; padding: 0; }
  html, body { width: 797px; height: 1200px; overflow: hidden; background: var(--white); }
  body { font-family: "Poppins", sans-serif; color: var(--text); position: relative; }

  .top-rule { position: absolute; left: 0; top: 0; width: 797px; height: 2px; background: var(--orange); }

  .site-header { position: absolute; left: 0; top: 2px; width: 797px; height: 76px; }
  .brand { position: absolute; left: 79px; top: 20px; display: flex; align-items: center; gap: 10px; }
  .brand-mark { width: 20px; height: 20px; background: var(--orange); border-radius: 3px; }
  .brand-name { font-size: 25px; font-weight: 600; color: var(--blue); letter-spacing: 0.5px; }

  .contact { position: absolute; left: 524px; top: 18px; display: flex; align-items: center; gap: 11px; }
  .contact-icon { width: 45px; height: 45px; border-radius: 7px; background: var(--orange);
    display: flex; align-items: center; justify-content: center; box-shadow: 2px 2px 0 #f8c2a5; }
  .contact-number { font-size: 22px; font-weight: 600; color: var(--blue); letter-spacing: 0.3px; }

  .hero { position: absolute; left: 0; top: 78px; width: 797px; height: 386px; }
  .hero-photo { position: absolute; inset: 0;
    background: linear-gradient(100deg, #b9b6b0 0%, #8a5550 22%, #6c3b3a 34%, #a9a49c 52%, #d8d3c8 70%, #c9b79a 86%, #9ea6ad 100%); }
  .hero-badge { position: absolute; left: 470px; top: 25px; width: 302px; height: 302px; border-radius: 50%;
    border: 5px solid var(--orange); background: rgba(255,255,255,0.86);
    display: flex; flex-direction: column; align-items: center; justify-content: center; text-align: center; padding: 0 28px; }
  .hero-title { font-size: 24px; font-weight: 400; color: var(--ink); line-height: 1.45; }
  .hero-copy { margin-top: 14px; font-size: 14.5px; font-weight: 300; color: var(--ink); line-height: 1.5; }
  .hero-rule { position: absolute; left: 0; top: 468px; width: 797px; height: 5px; background: var(--orange); }

  .features { position: absolute; left: 61px; top: 538px; width: 676px; display: grid;
    grid-template-columns: repeat(3, 204px); column-gap: 32px; row-gap: 70px; list-style: none; }
  .feature { height: 221px; background: var(--white); border-radius: 8px; box-shadow: var(--card-shadow);
    position: relative; text-align: center; }
  .feature-icon { position: absolute; left: 49px; top: 32px; width: 106px; height: 106px; border-radius: 50%;
    background: var(--orange-pale); display: flex; align-items: center; justify-content: center; }
  .feature-icon span { width: 94px; height: 94px; border-radius: 50%; background: var(--orange);
    display: flex; align-items: center; justify-content: center; }
  .feature-text { position: absolute; left: 0; right: 0; top: 162px; font-size: 14.5px; line-height: 1.4; color: var(--ink); padding: 0 10px; white-space: nowrap; }

  .footer-rule { position: absolute; left: 0; top: 1123px; width: 797px; height: 5px; background: var(--orange); }
  .site-footer { position: absolute; left: 0; top: 1135px; width: 797px; height: 65px; background: var(--footer);
    display: flex; align-items: center; justify-content: center; }
  .copyright { color: var(--white); font-size: 15px; font-weight: 400; letter-spacing: 0.3px; }
</style>
</head>
<body>
  <div class="top-rule"></div>

  <header class="site-header">
    <div class="brand"><span class="brand-mark"></span><span class="brand-name">RUVO WARE LTD</span></div>
    <div class="contact">
      <span class="contact-icon">
        <svg width="26" height="26" viewBox="0 0 24 24" fill="none" stroke="#fff" stroke-width="1.8" stroke-linecap="round" stroke-linejoin="round">
          <path d="M5 3h3l2 5-2.5 1.5a11 11 0 0 0 7 7L16 14l5 2v3a2 2 0 0 1-2 2A16 16 0 0 1 3 5a2 2 0 0 1 2-2z"/>
          <path d="M15 3a6 6 0 0 1 6 6M15 7a2 2 0 0 1 2 2"/>
        </svg>
      </span>
      <span class="contact-number">0161 555 0142</span>
    </div>
  </header>

  <section class="hero">
    <div class="hero-photo" role="img" aria-label="Photo of a pupil wearing a virtual reality headset in a classroom"></div>
    <div class="hero-badge">
      <h1 class="hero-title">Education, Support and Installation of All</h1>
      <p class="hero-copy">We offer fast, flexible, reliable and cost-effective ICT support for Education</p>
    </div>
  </section>
  <div class="hero-rule"></div>

  <ul class="features">
    <li class="feature">
      <div class="feature-icon"><span>
        <svg width="44" height="44" viewBox="0 0 40 40" fill="none" stroke="#fff" stroke-width="1.6" stroke-linecap="round" stroke-linejoin="round">
          <rect x="8" y="5" width="20" height="28" rx="1.5"/><path d="M12 11h12M12 15h12M12 19h8"/>
          <circle cx="14" cy="27" r="2.5"/><path d="M33 12l-9 13-2 4 3.5-2.5 9-13z"/>
        </svg></span></div>
      <p class="feature-text">ICT SLA agreements for as<br>little as £2000 per year</p>
    </li>
    <li class="feature">
      <div class="feature-icon"><span>
        <svg width="44" height="44" viewBox="0 0 40 40" fill="none" stroke="#fff" stroke-width="1.6" stroke-linecap="round" stroke-linejoin="round">
          <path d="M5 16l15-10 15 10v17H5z"/><path d="M5 16l15 10 15-10M5 33l11-9M35 33l-11-9"/>
          <circle cx="20" cy="15" r="3"/><path d="M23 15v1.5a1.5 1.5 0 0 0 3 0V15a6 6 0 1 0-2.5 4.8"/>
        </svg></span></div>
      <p class="feature-text">Unlimited Remote, phone<br>and email support</p>
    </li>
    <li class="feature">
      <div class="feature-icon"><span>
        <svg width="40" height="40" viewBox="0 0 24 24" fill="none" stroke="#fff" stroke-width="1.7" stroke-linecap="round" stroke-linejoin="round">
          <path d="M5 3h3l2 5-2.5 1.5a11 11 0 0 0 7 7L16 14l5 2v3a2 2 0 0 1-2 2A16 16 0 0 1 3 5a2 2 0 0 1 2-2z"/>
          <path d="M15 3a6 6 0 0 1 6 6M15 7a2 2 0 0 1 2 2"/>
        </svg></span></div>
      <p class="feature-text">Unlimited Call outs<br>included</p>
    </li>
    <li class="feature">
      <div class="feature-icon"><span>
        <svg width="46" height="46" viewBox="0 0 40 40" fill="none" stroke="#fff" stroke-width="1.6" stroke-linecap="round" stroke-linejoin="round">
          <path d="M5 12h30v5a3 3 0 0 0 0 6v5H5v-5a3 3 0 0 0 0-6z"/><path d="M12 12v16" stroke-dasharray="2 2"/>
          <path d="M17 17h12M17 21h12M17 25h8"/>
        </svg></span></div>
      <p class="feature-text">90% fix time within 30<br>minutes of ticket submission</p>
    </li>
    <li class="feature">
      <div class="feature-icon"><span>
        <svg width="44" height="44" viewBox="0 0 40 40" fill="none" stroke="#fff" stroke-width="1.6" stroke-linecap="round" stroke-linejoin="round">
          <path d="M10 5h15l6 6v23H10z"/><path d="M25 5v6h6"/>
          <circle cx="19" cy="20" r="5"/><path d="M22.5 23.5l5 5M14 30h6"/>
        </svg></span></div>
      <p class="feature-text">Extra support during<br>Scolvar inspections</p>
    </li>
    <li class="feature">
      <div class="feature-icon"><span>
        <svg width="44" height="44" viewBox="0 0 40 40" fill="none" stroke="#fff" stroke-width="1.6" stroke-linecap="round" stroke-linejoin="round">
          <path d="M20 4l12 4v10c0 8-5 13-12 16C13 31 8 26 8 18V8z"/>
          <path d="M15 22v-4a5 5 0 0 1 10 0M18 24v-6a2 2 0 0 1 4 0v4"/>
          <circle cx="28" cy="28" r="4.5"/><path d="M26 28l1.5 1.5 2.5-3"/>
        </svg></span></div>
      <p class="feature-text">GDPR service<br>included</p>
    </li>
  </ul>

  <div class="footer-rule"></div>
  <footer class="site-footer">
    <p class="copyright">Copyrights ©2022. All Rights Reserved</p>
  </footer>
</body>
</html>
```